Award-winnning Estate Agent needs a premium version of their 'For Sale' board design

We need a premium option for our 'For Sale' board design. We have a standard board that is attached to this brief, but were are looking to have a premium design version that we will use when selling exclusive properties. Our company name is Harbourline Vale Estates and the name for this is exclusive selection is: 'The Harbourline Collection'. The design needs to work with our current brand, but have a distinctive PREMIUM feel to it. I have uploaded the barnd guidelines and also some of the exisisting logo variations. We do NOT need a new logo but feel free to play around with colours, fonts, sizes etc. for the sign.

Target Market(s)

Property buyers & house hunters

Industry/Entity Type

Real Estate - Residential Property

Font styles to use
Sans Serif

Requirements
Must have
• A premium fee, must be square design, must be easy to read when driving past the sign
Nice to have
• I'm open ot ideas

```html
<!DOCTYPE html>
<html lang="en">
<head>
<meta charset="utf-8">
<title>Harbourline Vale Estates – For Sale Board</title>
<link href="https://fonts.googleapis.com/css2?family=Archivo:wght@400;600;800&family=Inter:wght@300&display=swap" rel="stylesheet">
<style>
  :root{
    --navy:#0a1c4f;
    --navy-deep:#071640;
    --navy-soft:#1a2f66;
    --gold:#a57c39;
    --gold-light:#c9985a;
    --board:#f3f3f2;
    --ink:#0b1d52;
    --page:#e6e6e6;
  }
  html,body{margin:0;padding:0;width:1200px;height:1200px;overflow:hidden;background:var(--page);}
  .board{
    position:relative;width:1200px;height:1200px;background:var(--board);
    font-family:"Archivo",Arial,sans-serif;box-sizing:border-box;
  }
  .brand-panel{
    position:absolute;left:40px;top:40px;width:1120px;height:720px;
    background:linear-gradient(160deg,var(--navy) 0%,var(--navy-deep) 100%);
    overflow:hidden;
  }
  .flourish{position:absolute;width:130px;height:340px;background:var(--navy-soft);opacity:.45;top:40px;}
  .flourish--left{left:0;border-radius:0 70px 70px 0;}
  .flourish--right{right:0;top:150px;border-radius:70px 0 0 70px;}
  .brand-name{
    position:absolute;left:0;right:0;top:330px;text-align:center;
    color:var(--gold-light);font-weight:600;font-size:80px;letter-spacing:1px;margin:0;
    white-space:nowrap;
  }
  .collection{
    position:absolute;left:240px;width:640px;height:100px;top:520px;text-align:center;
  }
  .collection svg{display:block;width:640px;height:100px;}
  .collection-title{
    position:absolute;left:0;right:0;top:30px;margin:0;
    font-family:"Inter",Arial,sans-serif;font-weight:300;font-size:34px;line-height:40px;
    color:var(--gold-light);text-transform:uppercase;white-space:nowrap;
  }
  .sale-band{
    position:absolute;left:40px;top:780px;width:1120px;height:210px;background:var(--gold);
    display:flex;align-items:center;justify-content:center;
  }
  .sale-band span{color:#fff;font-weight:800;font-size:176px;letter-spacing:4px;line-height:1;}
  .phone{
    position:absolute;left:0;right:0;top:1010px;text-align:center;margin:0;
    color:var(--ink);font-weight:800;font-size:96px;letter-spacing:2px;
  }
  .web{
    position:absolute;left:0;right:0;top:1115px;text-align:center;margin:0;
    color:var(--ink);font-weight:400;font-size:50px;letter-spacing:1px;white-space:nowrap;
  }
</style>
</head>
<body>
<div class="board">
  <section class="brand-panel">
    <div class="flourish flourish--left" role="img" aria-label="Faint ornamental flourish"></div>
    <div class="flourish flourish--right" role="img" aria-label="Faint ornamental flourish"></div>
    <h1 class="brand-name">Harbourline Vale Estates</h1>
    <div class="collection">
      <svg viewBox="0 0 640 100" aria-hidden="true">
        <line x1="10" y1="12" x2="630" y2="20" stroke="#c9985a" stroke-width="2"/>
        <line x1="10" y1="82" x2="630" y2="90" stroke="#c9985a" stroke-width="2"/>
      </svg>
      <p class="collection-title">The Harbourline Collection</p>
    </div>
  </section>
  <div class="sale-band"><span>FOR SALE</span></div>
  <p class="phone">01632 960412</p>
  <p class="web">www.harbourlinevaleestates.co.uk</p>
</div>
</body>
</html>
```